Looking to Redesign Brevonix.com website

You guys did one of the brochures for brevonix.com and I would like to see if we can go ahead and get an estimate for a redesigned web site for the company. We currently have a couple of pages on brevonix.com which are very much a starter type site.

The new design will need to reflect some of the things discussed in the brochure. It will have flash. Needs to be designed for simple hosting using cpanels.

The site needs to have between 12 and 15 pages with flash pages to move through features. Integrated with twitter like it is now, and contact forms delivered from our CRM along with other interactive features such as subscription to newsletter, etc...

I don't have lots of details on how to proceed yet, but here are some competitor sites:

Can we take a look at potential costs involved in the redo of the site as vague as my description above can permit.

Target Market(s)

Business to Business

Number of Pages Required

5+ page

Font styles to use
Sans Serif

Requirements
Must have
• Must have professional feel. Similar to brochure. and logo.
• Include our story in the discussion.
• embedded links to our CRM for popup contact forms.
• Logo files and 2 types of brochures uploaded.
• Important to keep color scheme
Nice to have
• Flash and some movement
Should not have
• Not sure yet

```html
<!DOCTYPE html>
<html lang="en">
<head>
<meta charset="utf-8">
<title>Brevonix – Hardware</title>
<link rel="stylesheet" href="https://fonts.googleapis.com/css2?family=Raleway:wght@400;500;600;700&family=Exo+2:ital,wght@1,800&display=swap">
<style>
:root{
  --red:#c10d0d;
  --red-dark:#a70808;
  --ink:#2b2b2b;
  --grey-title:#6d6d6d;
  --footer:#3d3d3d;
  --footer-dark:#2f2f2f;
  --line:#d9d9d9;
  --white:#fff;
}
*{box-sizing:border-box;margin:0;padding:0}
html,body{width:845px;height:1200px;overflow:hidden;background:var(--white)}
body{position:relative;font-family:"Raleway",sans-serif;color:var(--ink)}
.site-header{position:absolute;left:0;top:0;width:845px;height:103px;background:var(--white)}
.brand{position:absolute;display:flex;align-items:center;gap:8px;font-family:"Raleway",sans-serif;font-weight:700;font-size:20px;color:var(--red)}
.brand-dot{width:20px;height:20px;border-radius:50%;background:var(--red)}
.site-header .brand{left:53px;top:54px}
.contact-bar{position:absolute;top:22px;right:68px;display:flex;gap:0}
.contact-item{display:flex;align-items:center;gap:8px;padding:0 13px;border-left:1px solid #e5e5e5}
.contact-item:first-child{border-left:none}
.contact-item svg{width:22px;height:22px}
.contact-label{font-size:7px;color:#7a8aa0;letter-spacing:.3px;text-transform:uppercase}
.contact-value{font-size:9.5px;font-weight:700;color:#333;letter-spacing:.3px}
.contact-value.phone{font-size:12px;color:#444}
.main-nav{position:absolute;top:67px;right:57px;display:flex;align-items:center;gap:4px}
.main-nav a{font-size:9px;font-weight:700;color:#333;text-decoration:none;letter-spacing:.4px;padding:7px 12px;border-radius:14px}
.main-nav a.active{background:var(--red);color:var(--white)}
.hero{position:absolute;left:0;top:103px;width:845px;height:270px;background:linear-gradient(160deg,#f2f2f2 0%,#d9d9d9 45%,#5a5d63 70%,#3c3f45 100%)}
.hero-wave{position:absolute;left:0;top:280px;width:845px;height:100px}
.section-title{position:absolute;left:53px;top:402px;display:flex;align-items:center;gap:14px}
.section-title .mark{width:26px;height:26px;border-radius:50%;background:#c9c9c9}
.section-title h1{font-family:"Exo 2",sans-serif;font-style:italic;font-weight:800;font-size:22.5px;color:var(--red);letter-spacing:-.3px}
.card{position:absolute;width:361px;height:184px;border:1px solid var(--line);border-bottom:none;background:var(--white);overflow:hidden}
.card .product{position:absolute;border-radius:10px;background:linear-gradient(135deg,#9a9ea5,#45484e)}
.card h2{position:absolute;font-family:"Exo 2",sans-serif;font-style:italic;font-weight:800;font-size:17px;line-height:21px;color:var(--grey-title);text-transform:uppercase;white-space:nowrap}
.card svg.card-wave{position:absolute;left:-1px;bottom:0;width:361px;height:40px}
.site-footer{position:absolute;left:0;top:840px;width:845px;height:360px;background:linear-gradient(180deg,#555 0%,var(--footer) 40%,#2a2a2a 100%)}
.footer-swoosh{position:absolute;left:0;top:0;width:845px;height:150px}
.site-footer .brand{left:53px;top:180px;color:var(--white)}
.site-footer .brand-dot{background:var(--white)}
.footer-about{position:absolute;left:53px;top:225px;width:200px;font-size:10px;line-height:18px;color:#eee}
.footer-about a{display:block;margin-top:5px;font-weight:700;color:var(--white);text-decoration:none}
.footer-col{position:absolute;top:164px;height:160px;padding-left:21px;border-left:1px solid #4a4a4a}
.footer-col h3{font-size:10px;font-weight:700;color:var(--white);letter-spacing:.5px;margin-bottom:10px}
.quick-links{left:306px;width:260px}
.quick-links ul{list-style:none;display:grid;grid-template-columns:117px 100px;grid-auto-flow:column;grid-template-rows:repeat(4,21.5px)}
.quick-links a{font-size:9.5px;color:#ddd;text-decoration:none}
.newsletter{left:569px;width:240px}
.newsletter input{display:block;width:205px;height:26px;border:none;border-radius:13px;padding:0 16px;margin-bottom:6px;font-family:"Raleway",sans-serif;font-size:9.5px;color:#555}
.newsletter input::placeholder{color:#555}
.newsletter button{display:block;margin:8px 0 0 124px;width:81px;height:28px;border:none;border-radius:14px;background:linear-gradient(180deg,#d8140f,var(--red-dark));color:var(--white);font-family:"Raleway",sans-serif;font-size:10px;font-weight:600}
.footer-bottom{position:absolute;left:0;top:308px;width:845px;height:52px;background:var(--footer-dark);border-top:1px solid #505050}
.footer-bottom p{position:absolute;left:53px;top:20px;font-size:9px;color:#bbb}
.social{position:absolute;right:56px;top:13px;display:flex;gap:6px;list-style:none}
.social li{width:20px;height:20px;border-radius:50%;background:#8a8a8a}
</style>
</head>
<body>

<header class="site-header">
  <div class="brand"><span class="brand-dot"></span>Brevonix</div>
  <div class="contact-bar">
    <div class="contact-item">
      <svg viewBox="0 0 24 24" aria-hidden="true"><circle cx="12" cy="8" r="5" fill="#222"/><path d="M3 23c0-5 4-8 9-8s9 3 9 8z" fill="#222"/></svg>
      <div><div class="contact-label">Support</div><div class="contact-value">CHAT WITH US</div></div>
    </div>
    <div class="contact-item">
      <svg viewBox="0 0 24 24" aria-hidden="true"><rect x="2" y="5" width="20" height="14" rx="1" fill="none" stroke="#222" stroke-width="2"/><path d="M2 6l10 7 10-7" fill="none" stroke="#222" stroke-width="2"/></svg>
      <div><div class="contact-label">Email us at</div><div class="contact-value">SALES@BREVONIX.COM</div></div>
    </div>
    <div class="contact-item">
      <svg viewBox="0 0 24 24" aria-hidden="true"><path d="M7 2l3 4-2 3c1 3 3 5 5 6l2-2 4 3-2 4C10 20 4 13 4 4z" fill="#222"/></svg>
      <div><div class="contact-label">Call us now</div><div class="contact-value phone">8005550147</div></div>
    </div>
  </div>
  <nav class="main-nav">
    <a href="#">HOME</a><a href="#">WHY BREVONIX</a><a href="#">BENEFITS</a><a href="#">CASE STUDIES</a><a href="#" class="active">HARDWARE</a><a href="#">ABOUT US</a>
  </nav>
</header>

<div class="hero" role="img" aria-label="Photo of a conference speakerphone with extension microphone on a desk"></div>
<svg class="hero-wave" viewBox="0 0 845 100" preserveAspectRatio="none" aria-hidden="true">
  <path d="M0 18 C250 -4 520 72 845 52 L845 100 L0 100Z" fill="var(--red)"/>
  <path d="M0 22 C250 2 520 78 845 58 L845 100 L0 100Z" fill="#111"/>
  <path d="M0 36 C250 16 520 92 845 74 L845 100 L0 100Z" fill="#fff"/>
</svg>

<div class="section-title"><span class="mark"></span><h1>BEST OF CLASS HARDWARE</h1></div>

<article class="card" style="left:53px;top:454px">
  <div class="product" role="img" aria-label="Photo of a desk IP phone with colour screen" style="left:26px;top:28px;width:126px;height:102px"></div>
  <h2 style="left:176px;top:59px">Standard voice<br>access device</h2>
  <svg class="card-wave" viewBox="0 0 361 40" preserveAspectRatio="none" aria-hidden="true"><path d="M0 12 C120 0 230 34 361 14" fill="none" stroke="var(--red)" stroke-width="3"/><path d="M0 16 C120 4 230 38 361 18" fill="none" stroke="#111" stroke-width="3"/></svg>
</article>

<article class="card" style="left:435px;top:454px">
  <div class="product" role="img" aria-label="Photo of two desk phones with sidecar key modules" style="left:17px;top:16px;width:144px;height:130px"></div>
  <h2 style="left:175px;top:48px">Extended feature<br>or full access<br>device</h2>
  <svg class="card-wave" viewBox="0 0 361 40" preserveAspectRatio="none" aria-hidden="true"><path d="M0 14 C130 40 240 0 361 12" fill="none" stroke="var(--red)" stroke-width="3"/><path d="M0 18 C130 44 240 4 361 16" fill="none" stroke="#111" stroke-width="3"/></svg>
</article>

<article class="card" style="left:53px;top:650px">
  <div class="product" role="img" aria-label="Photo of a cordless handset in its charging base" style="left:45px;top:20px;width:72px;height:114px"></div>
  <h2 style="left:176px;top:57px">Wireless voice<br>access device</h2>
  <svg class="card-wave" viewBox="0 0 361 40" preserveAspectRatio="none" aria-hidden="true"><path d="M0 12 C120 0 230 34 361 14" fill="none" stroke="var(--red)" stroke-width="3"/><path d="M0 16 C120 4 230 38 361 18" fill="none" stroke="#111" stroke-width="3"/></svg>
</article>

<article class="card" style="left:435px;top:650px">
  <div class="product" role="img" aria-label="Photo of a conference phone with two extension microphones" style="left:11px;top:45px;width:184px;height:72px"></div>
  <h2 style="left:210px;top:57px">Conferencing<br>access device</h2>
  <svg class="card-wave" viewBox="0 0 361 40" preserveAspectRatio="none" aria-hidden="true"><path d="M0 14 C130 40 240 0 361 12" fill="none" stroke="var(--red)" stroke-width="3"/><path d="M0 18 C130 44 240 4 361 16" fill="none" stroke="#111" stroke-width="3"/></svg>
</article>

<footer class="site-footer">
  <svg class="footer-swoosh" viewBox="0 0 845 150" preserveAspectRatio="none" aria-hidden="true">
    <path d="M0 0 H845 V48 C560 92 250 56 0 8Z" fill="#fff"/>
    <path d="M0 8 C250 56 560 92 845 48 V84 C560 126 250 104 0 36Z" fill="#111" opacity=".55"/>
    <path d="M0 8 C250 56 560 92 845 48 V76 C560 116 250 94 0 30Z" fill="var(--red-dark)"/>
    <path d="M0 30 C250 94 560 116 845 76 V84 C560 126 250 104 0 38Z" fill="#1c1c1c"/>
  </svg>
  <div class="brand"><span class="brand-dot"></span>Brevonix</div>
  <p class="footer-about">Inter-Company Cloud Communications Platform...<a href="#">Read More</a></p>
  <section class="footer-col quick-links">
    <h3>QUICK LINKS</h3>
    <ul>
      <li><a href="#">Home</a></li><li><a href="#">Why Brevonix</a></li><li><a href="#">Benefits</a></li><li><a href="#">Case Studies</a></li>
      <li><a href="#">Hardware</a></li><li><a href="#">About Us</a></li><li><a href="#">Contact Us</a></li>
    </ul>
  </section>
  <section class="footer-col newsletter">
    <h3>NEWSLETTER SIGN UP</h3>
    <input type="text" placeholder="Enter Name">
    <input type="email" placeholder="Enter Email Address">
    <button type="button">SIGN UP</button>
  </section>
  <div class="footer-bottom">
    <p>© 2015-2016 brevonix. All Rights Reserved.</p>
    <ul class="social" aria-label="Social links">
      <li aria-label="Social profile"></li><li aria-label="Social profile"></li><li aria-label="Social profile"></li><li aria-label="News feed"></li>
    </ul>
  </div>
</footer>

</body>
</html>
```